Marwick Law Letterhead

We need a new letterhead design for a Law Firm. The address for the law firm is 1475 Calloway Street, Suite 210, Houston, Texas 77041. Phone Number: 832-361-9027; Fax Number: 832-614-7359. The logo is uploaded to the project.

```html
<!DOCTYPE html>
<html lang="en">
<head>
<meta charset="utf-8">
<title>Marwick Law Letterhead</title>
<link rel="stylesheet" href="https://fonts.googleapis.com/css2?family=Montserrat:wght@400;500&family=Libre+Baskerville:wght@400&display=swap">
<style>
  :root {
    --navy: #1c3160;
    --red: #d3232f;
    --paper: #ffffff;
    --backdrop: #e8e8e8;
    --ink: #3a3a3a;
    --ink-dark: #1f1f1f;
    --on-navy: #ffffff;
    --sign-tone: #d9d9d9;
  }
  * { box-sizing: border-box; margin: 0; padding: 0; }
  html, body {
    width: 1154px; height: 1200px; overflow: hidden;
    background: var(--backdrop);
    font-family: "Montserrat", Arial, sans-serif;
  }
  .letterhead {
    position: absolute; left: 172px; top: 34px;
    width: 810px; height: 1132px;
    background: var(--paper);
    box-shadow: 0 2px 10px rgba(0,0,0,0.25);
  }
  .header-band {
    position: absolute; left: 0; top: 0; width: 100%; height: 154px;
    background: var(--navy);
  }
  .brand {
    position: absolute; left: 25px; top: 32px; width: 258px; height: 78px;
    background: var(--paper);
    display: flex; align-items: center; gap: 14px; padding-left: 16px;
  }
  .brand-square { width: 40px; height: 40px; background: var(--navy); flex: none; }
  .brand-name {
    font-family: "Libre Baskerville", Georgia, serif;
    font-size: 26px; color: var(--navy); letter-spacing: 0.5px; white-space: nowrap;
  }
  .contact {
    position: absolute; left: 619px; top: 30px;
    color: var(--on-navy); font-size: 13.6px; line-height: 17.5px;
  }
  .contact-lines { list-style: none; margin-top: 12px; }
  .contact-lines li { display: flex; align-items: center; gap: 9px; height: 20px; }
  .contact-lines svg { width: 13px; height: 13px; flex: none; }
  .recipient {
    position: absolute; left: 31px; top: 266px;
    font-size: 13.6px; line-height: 20px; color: var(--ink-dark);
  }
  .letter-body {
    position: absolute; left: 31px; top: 352px; width: 751px;
    font-size: 13.5px; line-height: 20px; color: var(--ink);
    text-align: justify; hyphens: auto;
  }
  .letter-body p + p { margin-top: 20px; }
  .closing {
    position: absolute; left: 30px; top: 920px;
    font-size: 16.5px; color: var(--ink-dark);
  }
  .signature {
    position: absolute; left: 28px; top: 946px; width: 92px; height: 26px;
    background: linear-gradient(90deg, var(--sign-tone), #eeeeee);
    border-radius: 3px;
  }
</style>
</head>
<body>
  <main class="letterhead">
    <header class="header-band">
      <div class="brand">
        <span class="brand-square"></span>
        <span class="brand-name">Marwick Law</span>
      </div>
      <address class="contact" style="font-style:normal">
        <div>1475 Calloway Street,<br>Suite 210, Houston,<br>Texas 77041</div>
        <ul class="contact-lines">
          <li>
            <svg viewBox="0 0 24 24" aria-hidden="true"><path fill="#fff" d="M6.6 10.8a15.1 15.1 0 0 0 6.6 6.6l2.2-2.2a1 1 0 0 1 1-.25 11.4 11.4 0 0 0 3.6.57 1 1 0 0 1 1 1V20a1 1 0 0 1-1 1A17 17 0 0 1 3 4a1 1 0 0 1 1-1h3.5a1 1 0 0 1 1 1c0 1.25.2 2.45.57 3.6a1 1 0 0 1-.25 1z"/></svg>
            <span>832-361-9027</span>
          </li>
          <li>
            <svg viewBox="0 0 24 24" aria-hidden="true"><path fill="#fff" d="M6 2h12v6H6zM4 9h16a2 2 0 0 1 2 2v6h-4v5H6v-5H2v-6a2 2 0 0 1 2-2zm4 8v3h8v-3z"/></svg>
            <span>832-614-7359</span>
          </li>
        </ul>
      </address>
    </header>

    <section class="recipient">
      <div>Mr/s</div>
      <div>First Name and Last Name</div>
      <div>Company Name</div>
      <div>Address</div>
    </section>

    <section class="letter-body">
      <p>Lorem ipsum dolor sit amet,consectetur adipiscing sed do eiusmod tempor incididunt laboreet dolore magna aliqua.Ut enim ad minim.veniam, quis nostrud exercitation ullamco laboris nisi ut aliquip exea commodo consequat.Lorem ipsum dolor sit amet,consectetur adipiscing sed do eiusmod tempor incididunt.labore et dolore magna aliqua. Ut enim</p>
      <p>Lorem ipsum dolor sit amet, consectetur adipiscing sed do eiusmod tempor incididunt labore et dolore magna aliqua. Ut enim ad minim veniam, quis nostrud exercitation ullamco laboris nisi ut aliquip exea commodo consequat.Duis aute irure dolor in reprehenderit in voluptate velit esse cillum irure dolor in reprehenderit in voluptate velit esse irure</p>
      <p>Lorem ipsum dolor sit amet, consectetur adipiscing sed do eiusmod tempor incididunt labore et dolore magna aliqua. consequat. Duis aute irure dolor in.reprehenderit in voluptate velit esse cillum dolore eu fugiat nulla pariatur. Excepteur sint occaecat cupidatat non proident, sunt in culpa qui officia deserunt mollit,</p>
      <p>Lorem ipsum dolor sit amet, consectetur adipiscing sed do eiusmod tempor incididunt labore et dolore magna aliqua. Ut enim Lorem ipsum dolor sit amet, consectetur adipiscing sed do eiusmod tempor incididunt labore et dolore magna aliqua. Ut enim Lorem ipsum aliqua.ipsum</p>
      <p>Lorem ipsum dolor sit amet, consectetur adipiscing sed do eiusmod tempor incididunt labore et dolore magna aliqua. Ut enim ad minim veniam, quis nostrud exercitation ullamco laboris nisi ut aliquip exea commodo consequat.Duis aute irure dolor in reprehenderit in voluptate velit esse cillum irure dolor in reprehenderit in voluptate velit esse irure</p>
      <p>Lorem ipsum dolor sit amet, consectetur adipiscing sed do eiusmod tempor incididunt labore et dolore magna aliqua. Ut enim ad minim veniam, quis nostrud exercitation ullamco laboris nisi ut aliquip exea commodo consequat.Duis aute irure dolor in reprehenderit in voluptate velit esse cillum irure dolor in reprehenderit in voluptate velit esse irure</p>
    </section>

    <div class="closing">Regards</div>
    <div class="signature" role="img" aria-label="Handwritten signature of the sender"></div>
  </main>
</body>
</html>
```